Realtor branding business card

modern, simple and self branding. Broker office logo needs to be used but not emphasized. Looking to brand myself

Target Market(s)

buyers, sellers and investors

Industry/Entity Type

Realtor

Contact Information for Business Card

Sample of my current business card on file

Requirements
Must have
• my website - tobiasmerrowkl.com
• Realtor logo
• Fair housing logo
Nice to have
• Colors from office logo but not a must
Should not have
• Do not want headshot

```html
<!DOCTYPE html>
<html lang="en">
<head>
<meta charset="utf-8">
<title>Tobias Merrow — Realtor Business Card</title>
<link rel="stylesheet" href="https://fonts.googleapis.com/css2?family=Montserrat:wght@400;500;700;800&display=swap">
<style>
  :root {
    --bg: #151515;
    --card: #262626;
    --card-edge: #2e2e2e;
    --ink: #f2f2f2;
    --ink-soft: #d9d9d9;
    --accent: #e0262b;
    --emboss: #3a3a3a;
  }
  * { margin: 0; padding: 0; box-sizing: border-box; }
  html, body {
    width: 1200px; height: 900px; overflow: hidden;
    background: var(--bg);
    font-family: "Montserrat", sans-serif;
    color: var(--ink);
  }
  .canvas {
    width: 1200px; height: 900px;
    display: flex; flex-direction: column; align-items: center; justify-content: center;
    gap: 36px;
  }
  .card {
    width: 700px; height: 400px;
    background: linear-gradient(160deg, var(--card-edge), var(--card));
    position: relative;
  }

  /* Front side */
  .card--front {
    display: flex; flex-direction: column; align-items: center; justify-content: center;
  }
  .front-brand {
    font-weight: 800; font-size: 44px; letter-spacing: 0.5px;
    color: var(--emboss);
    margin-top: -20px;
  }
  .front-web {
    position: absolute; bottom: 60px; left: 0; right: 0;
    text-align: center; font-size: 17px; letter-spacing: 0.5px; color: var(--ink);
  }
  .accent { color: var(--accent); }

  /* Back side */
  .card--back { display: flex; align-items: center; }
  .brokerage {
    width: 330px; padding-left: 56px;
    display: flex; align-items: center; gap: 12px;
  }
  .brokerage-mark { width: 14px; height: 14px; background: var(--accent); flex: none; }
  .brokerage-name {
    font-weight: 800; font-size: 30px; line-height: 1.1; color: var(--ink);
  }
  .divider { width: 2px; height: 230px; background: var(--accent); }
  .agent { padding-left: 40px; }
  .agent-name {
    font-weight: 700; font-size: 22px; letter-spacing: 1px;
    text-transform: uppercase; color: var(--accent);
  }
  .agent-title { font-size: 17px; color: var(--ink-soft); margin-bottom: 18px; }
  .contact-list { list-style: none; }
  .contact-item {
    display: flex; align-items: center; gap: 12px;
    font-size: 18px; line-height: 1.45; letter-spacing: 0.5px;
  }
  .contact-icon { width: 14px; height: 14px; flex: none; }
  .address { margin-top: 14px; font-size: 18px; line-height: 1.4; letter-spacing: 0.3px; }
</style>
</head>
<body>
<main class="canvas">

  <section class="card card--front">
    <div class="front-brand">Brightway Realty Group</div>
    <p class="front-web">www.<span class="accent">tobiasmerrowkl</span>.com</p>
  </section>

  <section class="card card--back">
    <div class="brokerage">
      <span class="brokerage-mark"></span>
      <span class="brokerage-name">Brightway<br>Realty Group</span>
    </div>
    <div class="divider"></div>
    <div class="agent">
      <h1 class="agent-name">Tobias Merrow</h1>
      <p class="agent-title">Realtor</p>
      <ul class="contact-list">
        <li class="contact-item">
          <svg class="contact-icon" viewBox="0 0 14 14"><rect x="3.5" y="1" width="7" height="12" rx="1.2" fill="none" stroke="var(--accent)" stroke-width="1.3"/><line x1="6" y1="11" x2="8" y2="11" stroke="var(--accent)" stroke-width="1.2"/></svg>
          407. 555. 0147
        </li>
        <li class="contact-item">
          <svg class="contact-icon" viewBox="0 0 14 14"><path d="M3 1.5 L5.5 4 L4.3 5.6 Q5.5 8.5 8.4 9.7 L10 8.5 L12.5 11 L11 12.6 Q5 12 1.4 3 Z" fill="var(--accent)"/></svg>
          407. 555. 0190
        </li>
        <li class="contact-item">
          <svg class="contact-icon" viewBox="0 0 14 14"><rect x="1" y="3" width="12" height="8.5" fill="none" stroke="var(--accent)" stroke-width="1.3"/><polyline points="1,3 7,8 13,3" fill="none" stroke="var(--accent)" stroke-width="1.3"/></svg>
          info@tobiasmerrowkl.com
        </li>
        <li class="contact-item">
          <svg class="contact-icon" viewBox="0 0 14 14"><circle cx="7" cy="7" r="5.8" fill="none" stroke="var(--accent)" stroke-width="1.2"/><ellipse cx="7" cy="7" rx="2.5" ry="5.8" fill="none" stroke="var(--accent)" stroke-width="1"/><line x1="1.2" y1="7" x2="12.8" y2="7" stroke="var(--accent)" stroke-width="1"/></svg>
          www.<span class="accent">tobiasmerrowkl</span>.com
        </li>
      </ul>
      <p class="address">480 Lakeview Court<br>Maple Springs, FL 32000</p>
    </div>
  </section>

</main>
</body>
</html>
```